holloway paving service

Needs to have phone number 0418259730 and email markholloway@brightmail.com.au.
ABN 62318470915
name mark holloway

For all your concreting solutions
Excavation
Exposed & colour concrete
House & shed slabs
Driveways
Landing & steps

Contact Information for Business Card

ph 0418259730
email markholloway@brightmail.com.au.
ABN 62318470915
name mark holloway

```html
<!DOCTYPE html>
<html lang="en">
<head>
<meta charset="utf-8">
<title>Holloway Paving Service – Business Card</title>
<link rel="stylesheet" href="https://fonts.googleapis.com/css2?family=Lato:wght@400;700&display=swap">
<style>
  :root {
    --bg: #2a2a2a;
    --card-white: #ffffff;
    --orange: #f26a22;
    --grey: #666666;
    --text: #333333;
    --rule: #666666;
  }
  * { margin: 0; padding: 0; box-sizing: border-box; }
  html, body { width: 1200px; height: 1200px; overflow: hidden; }
  body {
    background: var(--bg);
    font-family: "Lato", sans-serif;
    position: relative;
  }
  .card {
    position: absolute;
    top: 310px;
    height: 594px;
  }
  .card-front {
    left: 234px;
    width: 364px;
    background: var(--card-white);
    color: var(--text);
  }
  .card-back {
    left: 627px;
    width: 369px;
    background: linear-gradient(to bottom, var(--grey) 0 297px, var(--orange) 297px 100%);
    display: flex;
    flex-direction: column;
    align-items: center;
    justify-content: center;
  }

  /* Front – brand lockup */
  .brand {
    position: absolute;
    top: 125px;
    left: 36px;
    display: flex;
    align-items: center;
  }
  .brand-square {
    width: 58px;
    height: 58px;
    background: var(--orange);
    flex: none;
  }
  .brand-divider {
    width: 2px;
    height: 82px;
    background: var(--orange);
    margin: 0 8px 0 22px;
  }
  .brand-name {
    color: var(--orange);
    font-weight: 700;
    font-size: 17px;
    line-height: 1.25;
    letter-spacing: 0.2px;
    text-transform: uppercase;
  }

  /* Front – contact block */
  .contact {
    position: absolute;
    top: 298px;
    left: 0;
    width: 100%;
    text-align: center;
  }
  .person-name {
    font-size: 21px;
    font-weight: 700;
    text-transform: uppercase;
    letter-spacing: 0.3px;
  }
  .person-name .first { color: var(--orange); }
  .person-name .last { color: var(--grey); }
  .abn { font-size: 16px; margin-top: 8px; }
  .rule {
    width: 207px;
    height: 1px;
    background: var(--rule);
    margin: 16px auto;
  }
  .details p { font-size: 16px; line-height: 22px; }
  .tagline {
    color: var(--orange);
    font-size: 15px;
    font-weight: 700;
    text-transform: uppercase;
    margin-top: 10px;
  }
  .services {
    list-style: none;
    font-size: 16px;
    line-height: 21.5px;
    margin-top: 8px;
  }

  /* Back */
  .back-square {
    width: 44px;
    height: 44px;
    background: var(--card-white);
    margin-bottom: 22px;
  }
  .back-name {
    color: var(--card-white);
    font-weight: 700;
    font-size: 34px;
    line-height: 1.2;
    text-align: center;
    text-transform: uppercase;
    letter-spacing: 1px;
  }
</style>
</head>
<body>
  <section class="card card-front" aria-label="Business card front">
    <div class="brand">
      <span class="brand-square"></span>
      <span class="brand-divider"></span>
      <span class="brand-name">Holloway Paving<br>Service</span>
    </div>

    <div class="contact">
      <h1 class="person-name"><span class="first">Mark</span> <span class="last">Holloway</span></h1>
      <p class="abn">ABN 62318470915</p>
      <div class="rule"></div>
      <div class="details">
        <p>0418259730</p>
        <p>markholloway@brightmail.com.au</p>
      </div>
      <div class="rule"></div>
      <p class="tagline">For all your concreting solutions</p>
      <ul class="services">
        <li>Excavation &nbsp;| Exposed &amp; colour concrete</li>
        <li>House &amp; shed slabs | Driveways</li>
        <li>Landing &amp; steps</li>
      </ul>
    </div>
  </section>

  <section class="card card-back" aria-label="Business card back">
    <span class="back-square"></span>
    <p class="back-name">Holloway<br>Paving<br>Service</p>
  </section>
</body>
</html>
```